Business card por a urban DJ, up scale audience target

Need a sober design, modern, conservative colors but i can consider some options, y play rnb, hip hop, EDM and top40.

Business card for contact and personal info, double sided, use logo attrached please; im 42 so i need a card acording to my age an target audience.

Target Market(s)

Adult people, up scale audience

Industry/Entity Type

Music Download

Contact Information for Business Card

Cel (318) 4207265518 www.lumadrift.com

Requirements
Must have
• open mind
Nice to have
• open mind
Should not have
• DJ

```html
<!DOCTYPE html>
<html lang="en">
<head>
<meta charset="utf-8">
<title>Luma — Business Card</title>
<link href="https://fonts.googleapis.com/css2?family=Arimo:wght@400;700&display=swap" rel="stylesheet">
<style>
  :root {
    --stage: #e4e2de;
    --card-white: #ffffff;
    --card-black: #161616;
    --ink: #111111;
    --ink-soft: #8a8a8a;
    --mark-dark: #2c2c2c;
    --mark-light: #e6e6e6;
    --url-light: #d0d0d0;
  }
  * { box-sizing: border-box; margin: 0; padding: 0; }
  html, body {
    width: 1200px; height: 950px; overflow: hidden;
    background: var(--stage);
    font-family: "Arimo", Arial, sans-serif;
  }
  .sheet {
    width: 1200px; height: 950px;
    display: flex; flex-direction: column;
    align-items: center; justify-content: center; gap: 50px;
  }
  .card {
    width: 700px; height: 400px;
    position: relative;
    box-shadow: 0 6px 18px rgba(0,0,0,0.18);
  }
  /* Back side */
  .card--back {
    background: linear-gradient(160deg, #232323 0%, var(--card-black) 60%, #0d0d0d 100%);
    display: flex; flex-direction: column; align-items: center; justify-content: center;
  }
  .card--back .wordmark {
    font-size: 120px; font-weight: 700; letter-spacing: 4px;
    color: var(--mark-light); line-height: 1;
  }
  .card--back .site {
    margin-top: 22px;
    font-size: 22px; letter-spacing: 5px;
    color: var(--url-light);
  }
  /* Front side */
  .card--front {
    background: linear-gradient(170deg, var(--card-white) 0%, #f6f6f6 70%, #e9e9e9 100%);
  }
  .contact {
    position: absolute; left: 56px; top: 110px;
    width: 330px;
  }
  .contact__row {
    display: flex; align-items: flex-start; gap: 20px;
  }
  .contact__row + .contact__row { margin-top: 20px; }
  .icon {
    width: 26px; height: 26px; flex: none;
    background: var(--ink); border-radius: 3px;
    display: flex; align-items: center; justify-content: center;
  }
  .icon svg { width: 18px; height: 18px; }
  .person__name {
    font-size: 28px; font-weight: 700; color: var(--ink);
    letter-spacing: 1px; line-height: 1; white-space: nowrap;
  }
  .person__role {
    margin-top: 8px;
    font-size: 20px; color: var(--ink-soft); letter-spacing: 1px;
  }
  .contact__text {
    font-size: 25px; color: var(--ink); line-height: 26px; white-space: nowrap;
  }
  .row--person { margin-bottom: 8px; }
  .card--front .wordmark {
    position: absolute; right: 48px; top: 132px;
    width: 250px; text-align: right;
    font-size: 78px; font-weight: 700; letter-spacing: 2px;
    color: var(--mark-dark); line-height: 1;
  }
</style>
</head>
<body>
<main class="sheet">

  <section class="card card--back" aria-label="Card back">
    <div class="wordmark">LUMA</div>
    <div class="site">LUMADRIFT.COM</div>
  </section>

  <section class="card card--front" aria-label="Card front">
    <div class="contact">
      <div class="contact__row row--person">
        <span class="icon">
          <svg viewBox="0 0 18 18" aria-hidden="true">
            <circle cx="9" cy="6" r="3.6" fill="#fff"/>
            <path d="M2.5 16c0-3.6 2.9-5.8 6.5-5.8s6.5 2.2 6.5 5.8z" fill="#fff"/>
          </svg>
        </span>
        <div class="person">
          <div class="person__name">MARC ELLISON</div>
          <div class="person__role">PRESIDENT</div>
        </div>
      </div>
      <div class="contact__row">
        <span class="icon">
          <svg viewBox="0 0 18 18" aria-hidden="true">
            <path d="M4.2 2.5l2.4-.4 1.3 3.2-1.6 1.2c.8 1.7 2 3 3.7 3.8l1.2-1.6 3.2 1.3-.4 2.4c-.2.8-.9 1.3-1.7 1.2C7.6 13.2 4.8 10.4 4.4 5.6c-.1-.9.4-2.6-.2-3.1z" fill="#fff"/>
          </svg>
        </span>
        <span class="contact__text">(318) 4207265518</span>
      </div>
      <div class="contact__row">
        <span class="icon">
          <svg viewBox="0 0 18 18" aria-hidden="true">
            <circle cx="9" cy="9" r="6.5" fill="none" stroke="#fff" stroke-width="1.5"/>
            <ellipse cx="9" cy="9" rx="2.8" ry="6.5" fill="none" stroke="#fff" stroke-width="1.2"/>
            <line x1="2.5" y1="9" x2="15.5" y2="9" stroke="#fff" stroke-width="1.2"/>
          </svg>
        </span>
        <span class="contact__text">www.lumadrift.com</span>
      </div>
    </div>
    <div class="wordmark">LUMA</div>
  </section>

</main>
</body>
</html>
```